Brand Identity & Marketing Website Design for Professional Football Scouting Software

Merivantalo is a professional football scouting report generation software.
It is a standalone desktop application that allows football clubs, agencies and players to generate structured, executive-level A4 PDF scouting reports.
This is NOT:
a betting platform
a fan website
a football news blog
a SaaS subscription platform
This is a premium document-generation software tool designed for professional use inside football organizations.
The brand must reflect:
• Structure
• Authority
• Precision
• Professionalism
• Trust
• Executive-level quality
Think consulting firm, performance analysis tool, structured business software.
Not flashy sports media.
What We Need
We are looking for:
1️⃣ Logo Design
2️⃣ Full Brand Identity System
3️⃣ Marketing Website UI/UX Design
(Development is NOT included in this job.)
Important Product Context
Merivantalo is sold as a one-time purchase software package.
After purchase: • Customers download the software
• Install it locally
• Generate reports offline
There is no recurring subscription.
There is no SaaS login platform.
The website is a marketing and purchase website only.
1️⃣ Logo Design
The logo must:
• Be professional and timeless
• Work in both light and dark backgrounds
• Be scalable (website header, app icon, favicon)
• Avoid cliché football logo styles (no shields, mascots, flashy emblems)
• Feel modern, clean, and strong
We prefer:
• Clean typography-based logo
• Minimal symbol integration
• Strong visual balance
• Suitable for software branding
Name:
Merivantalo
Optional tagline:
The leading platform for professional football scouting reports
Deliver:
• Full logo
• Icon-only version (for desktop app icon)
• Light & dark variations
2️⃣ Brand Identity System
We need a structured design system that supports:
• Marketing website
• Desktop application UI
• PDF report previews
Please define:
• Primary color palette
• Secondary color palette
• Accent colors
• Typography system (professional, highly readable)
• Heading hierarchy
• UI styling guidelines
• Light mode & dark mode principles
The design must feel:
• Minimal
• Grid-based
• Clean
• Premium
• Corporate
Avoid:
• Neon colors
• Heavy gradients
• Overly sporty visuals
• Gaming aesthetics
3️⃣ Marketing Website Design (UI/UX Only)
We need full website design in Figma for:
• Homepage
• Product Overview
• Packages Page (Club / Agency / Player)
• How It Works
• Demo Section
• FAQ
• Contact
• Purchase / Download Page
Design must include:
• Hero section
• Feature explanation sections
• Structured benefits
• Product screenshots placement
• Pricing comparison layout
• Clear call-to-action areas
• Professional footer
Responsive design required (Desktop-first, mobile adaptation).
Important:
Content copy will be provided by us.
Designer focuses on layout, structure, hierarchy and visual design.
Target Audience
• Professional football clubs
• Scouting departments
• Player agencies
• Semi-professional and professional players
This is primarily B2B, with some B2C.
Style Direction
We are looking for:
• Strong typography
• Balanced whitespace
• Structured layouts
• Subtle but confident use of color
• Professional photography (if used)
• Premium software feel
The website and brand must feel trustworthy and high-level.
Deliverables
• Logo files (AI, SVG, PNG)
• Brand guideline document (PDF)
• Figma file with full website UI
• Icon assets (app icon, favicon)
• Color and typography system

Need extra days to review

```html
<!DOCTYPE html>
<html lang="en">
<head>
<meta charset="utf-8">
<title>Merivantalo — Professional Football Scouting Reports</title>
<link rel="stylesheet" href="https://fonts.googleapis.com/css2?family=Orbitron:wght@400;500;700;800&family=Inter:wght@400;500;600;700&display=swap">
<style>
:root{
  --navy:#232945;
  --navy-deep:#1c2139;
  --ink:#1d2030;
  --muted:#5d6274;
  --line:#d9dce6;
  --hero-bg:#eceef3;
  --lavender:#eceef9;
  --lavender-2:#e3e6f6;
  --steel:#7c85a5;
  --steel-light:#9aa2bf;
  --white:#ffffff;
  --num:#d5d8e2;
}
*{box-sizing:border-box;margin:0;padding:0}
html,body{width:1200px;height:5332px;overflow:hidden}
body{position:relative;background:var(--white);font-family:"Inter",Arial,sans-serif;color:var(--ink)}
.abs{position:absolute}
.display{font-family:"Orbitron","Arial Black",sans-serif;text-transform:uppercase;letter-spacing:2px}
.btn{display:inline-flex;align-items:center;justify-content:center;background:var(--navy);color:var(--white);font-size:12px;font-weight:600;text-transform:uppercase;letter-spacing:.6px;height:38px;padding:0 22px;border-radius:3px;white-space:nowrap}
.section-title{position:absolute;left:0;width:1200px;text-align:center;font-size:40px;color:var(--ink)}
.section-title b{font-weight:800}
.section-title span{font-weight:400}
.placeholder{position:absolute}

/* header */
.site-header .brand{left:132px;top:50px;display:flex;align-items:center;gap:10px;font-size:30px;font-weight:600;color:var(--navy)}
.brand-mark{width:26px;height:26px;background:var(--navy);border-radius:4px}
.top-actions{left:700px;top:24px;display:flex;gap:10px}
.top-actions .btn{height:30px;font-size:11px}
.main-nav{left:552px;top:78px;display:flex;gap:22px;font-size:12px;font-weight:600;text-transform:uppercase;color:var(--ink)}
.main-nav .active{border-bottom:2px solid var(--navy);padding-bottom:4px}

/* hero */
.hero-title{left:132px;top:222px;font-size:40px;line-height:48px;color:var(--navy);letter-spacing:3px}
.hero-title .l1{font-weight:800}
.hero-title .l2{font-weight:400}
.hero-title .l3{font-weight:800}
.hero-text{left:132px;top:410px;width:600px;font-size:16px;line-height:27px;color:var(--ink)}
.hero-actions{left:132px;top:510px;display:flex;gap:14px}
.hero-note{left:132px;top:596px;font-size:15px;color:var(--ink)}
.scroll-cue{left:584px;top:712px}

/* products */
.feature-card{background:var(--white);border-radius:6px;box-shadow:0 8px 26px rgba(35,41,69,.16);padding:32px 40px}
.feature-card h3{font-size:18px;font-weight:700;margin-bottom:16px}
.feature-card ul{list-style:none}
.feature-card li{font-size:14px;line-height:25px;color:var(--muted)}
.feature-card li::before{content:"•";margin-right:8px;color:var(--ink)}
.feature-card.accent{border-left:6px solid var(--navy)}

/* packages */
.price-card{background:var(--white);border-radius:6px;box-shadow:0 4px 18px rgba(35,41,69,.12);padding:22px 22px 26px;text-align:left}
.price-card.featured{box-shadow:0 12px 32px rgba(35,41,69,.22)}
.plan-tag{height:32px;border-radius:4px;background:linear-gradient(180deg,var(--steel-light),var(--steel));color:var(--white);font-size:15px;font-weight:600;display:flex;align-items:center;justify-content:center;text-transform:uppercase;margin-bottom:28px}
.price{font-size:34px;font-weight:700;margin:0 0 18px 14px}
.price small{font-size:22px;font-weight:600}
.price-divider{height:1px;background:var(--line);margin-bottom:18px}
.price-card ul{list-style:none;margin-left:14px}
.price-card li{font-size:15px;line-height:36px;color:var(--ink)}
.price-card li::before{content:"";display:inline-block;width:7px;height:7px;border-radius:50%;background:var(--ink);margin-right:12px;vertical-align:middle}
.price-card .btn{width:222px;margin:26px 0 0 14px;height:38px}

/* how it works */
.step{position:absolute;width:260px}
.step h4{font-size:13px;font-weight:700;text-transform:uppercase;height:18px;line-height:18px;white-space:nowrap}
.step .rule{height:3px;background:var(--navy);margin:6px 0 8px;border-radius:2px}
.step p{font-size:12px;line-height:17px;color:var(--muted)}
.step.left{text-align:right}
.step-icon{position:absolute;width:60px;height:60px}
.step-num{position:absolute;font-family:"Orbitron",sans-serif;font-size:42px;line-height:50px;font-weight:500;color:var(--num)}

/* demo */
.demo-form .field{position:absolute;height:52px;border:1px solid #bfc3d3;border-radius:3px;background:var(--white);font-size:14px;color:var(--ink);padding:16px 12px}
.demo-form .field.area{height:124px}

/* faq */
.faq-item{position:absolute;left:228px;width:744px;height:56px;background:var(--white);border-radius:4px;box-shadow:0 3px 12px rgba(35,41,69,.14);display:flex;align-items:center;padding:0 28px;font-size:14px;font-weight:600}
.faq-item .toggle{position:absolute;right:18px;top:14px;width:28px;height:28px;border-radius:50%;background:var(--navy-deep)}
.faq-item.open{height:140px;align-items:flex-start;flex-direction:column;padding-top:20px;border-left:5px solid var(--navy)}
.faq-item.open p{font-size:12px;font-weight:400;line-height:18px;color:var(--muted);margin-top:16px;width:680px}

/* footer */
.site-footer{left:0;top:4880px;width:1200px;height:452px;color:var(--white)}
.contact-row{position:absolute;top:132px;left:0;width:1200px;display:flex;justify-content:center;gap:120px;align-items:center;font-size:13px}
.contact-item{display:flex;align-items:center;gap:12px}
.contact-item .ic{width:40px;height:40px;border-radius:50%;background:var(--white);display:flex;align-items:center;justify-content:center}
.contact-item.phone{font-size:20px;font-weight:700}
.footer-nav{position:absolute;top:244px;left:0;width:1200px;display:flex;justify-content:center;gap:30px;font-size:15px;font-weight:500;text-transform:uppercase}
.footer-rule{position:absolute;top:290px;left:150px;width:900px;height:1px;background:rgba(255,255,255,.18)}
.copyright{position:absolute;top:304px;left:0;width:1200px;text-align:center;font-size:13px}
.socials{position:absolute;top:366px;left:0;width:1200px;display:flex;justify-content:center;gap:12px}
.socials span{width:34px;height:34px;border-radius:50%;border:2px solid var(--white)}
</style>
</head>
<body>

<!-- HERO BACKGROUND -->
<svg class="abs" style="left:0;top:0" width="1200" height="860" viewBox="0 0 1200 860" aria-hidden="true">
  <path d="M0 0H1200V690C1010 790 760 835 560 805C360 775 160 700 0 720Z" fill="#eceef3"/>
  <path d="M0 740C220 700 420 790 620 820C820 850 1020 810 1200 720" fill="none" stroke="#e1e4ec" stroke-width="2"/>
</svg>

<header class="site-header">
  <div class="abs brand"><span class="brand-mark"></span>Merivantalo</div>
  <div class="abs top-actions">
    <span class="btn">Contact us</span>
    <span class="btn">Purchase software</span>
  </div>
  <nav class="abs main-nav">
    <span class="active">Home</span><span>Product</span><span>Packages</span><span>Demo</span><span>How it works</span><span>FAQ'S</span>
  </nav>
</header>

<section class="hero">
  <h1 class="abs hero-title display">
    <div class="l1">Professional football</div>
    <div class="l2">Scouting reports. Structured.</div>
    <div class="l3">Executive. Precise.</div>
  </h1>
  <p class="abs hero-text">Merivantalo is a standalone desktop software designed for football clubs, agencies and professionals to generate structured A4 executive-level scouting reports.</p>
  <div class="abs hero-actions">
    <span class="btn">View demo report</span>
    <span class="btn">Purchase software</span>
  </div>
  <p class="abs hero-note">One-time purchase • Offline use • No subscription</p>
  <div class="placeholder" role="img" aria-label="Laptop showing the Merivantalo report dashboard" style="left:780px;top:320px;width:420px;height:320px;border-radius:10px 0 0 10px;background:linear-gradient(160deg,#2b3150,#1b2036 55%,#c9ccd6 56%,#e6e8ee)"></div>
  <svg class="abs scroll-cue" width="32" height="48" viewBox="0 0 32 48" aria-hidden="true">
    <rect x="6" y="2" width="20" height="32" rx="10" fill="none" stroke="#232945" stroke-width="2"/>
    <line x1="16" y1="9" x2="16" y2="16" stroke="#232945" stroke-width="2"/>
    <path d="M10 40l6 5 6-5" fill="none" stroke="#232945" stroke-width="2"/>
  </svg>
</section>

<!-- PRODUCTS -->
<section class="products">
  <h2 class="section-title display" style="top:964px"><b>Our</b> <span>Products</span></h2>
  <div class="placeholder" role="img" aria-label="Analyst presenting scouting data on a large screen" style="left:144px;top:1072px;width:396px;height:410px;border-radius:4px;background:linear-gradient(135deg,#2e6f9e,#9cc3dc 55%,#d8dde4)"></div>
  <div class="abs feature-card accent" style="left:600px;top:1072px;width:460px;height:250px">
    <h3>Structured Report Engine</h3>
    <ul><li>Automated executive report formatting</li><li>Structured data input modules</li><li>Clean A4 PDF export</li><li>Standardized professional templates</li></ul>
  </div>
  <div class="abs feature-card" style="left:600px;top:1344px;width:452px;height:248px">
    <h3>Built for Professional Environments</h3>
    <ul><li>Works fully offline</li><li>Desktop installed software</li><li>Secure internal usage</li><li>No cloud dependency</li></ul>
  </div>
</section>

<!-- PACKAGES BACKGROUND -->
<svg class="abs" style="left:0;top:1600px" width="1200" height="820" viewBox="0 0 1200 820" aria-hidden="true">
  <path d="M0 200C260 40 700 20 1200 150V700C900 810 400 800 0 640Z" fill="#eceef9"/>
  <path d="M0 230C300 80 720 60 1200 190" fill="none" stroke="#dfe2f3" stroke-width="2"/>
</svg>

<section class="packages">
  <h2 class="section-title display" style="top:1708px"><b>Our</b> <span>Packages</span></h2>
  <div class="abs price-card" style="left:152px;top:1812px;width:276px;height:448px">
    <div class="plan-tag">Club</div>
    <div class="price">$67.89<small>/Mo</small></div>
    <div class="price-divider"></div>
    <ul><li>Sed ut perspiciatis</li><li>Unde omnis iste</li><li>Nnatus errvoluptatem</li><li>Accusantium dolque</li><li>Nemo enim ipsam</li></ul>
    <span class="btn">Purchase</span>
  </div>
  <div class="abs price-card featured" style="left:452px;top:1804px;width:300px;height:468px">
    <div class="plan-tag">Agency</div>
    <div class="price">$77.89<small>/Mo</small></div>
    <div class="price-divider"></div>
    <ul><li>Sed ut perspiciatis</li><li>Unde omnis iste</li><li>Nnatus errvoluptatem</li><li>Accusantium dolque</li><li>Nemo enim ipsam</li></ul>
    <span class="btn" style="width:246px">Purchase</span>
  </div>
  <div class="abs price-card" style="left:772px;top:1812px;width:276px;height:448px">
    <div class="plan-tag">Player</div>
    <div class="price">$87.89<small>/Mo</small></div>
    <div class="price-divider"></div>
    <ul><li>Sed ut perspiciatis</li><li>Unde omnis iste</li><li>Nnatus errvoluptatem</li><li>Accusantium dolque</li><li>Nemo enim ipsam</li></ul>
    <span class="btn">Purchase</span>
  </div>
</section>

<!-- HOW IT WORKS -->
<section class="how-it-works">
  <h2 class="section-title display" style="top:2584px"><b>How</b> <span>it works</span></h2>

  <!-- row 1 -->
  <div class="step left" style="left:170px;top:2724px"><h4>Download software</h4><div class="rule"></div><p>Sed ut perspiciatis unde omnis iste<br>natus error sit voluptatem</p></div>
  <svg class="step-icon" style="left:446px;top:2716px" viewBox="0 0 60 60" aria-hidden="true" fill="none" stroke="#232945" stroke-width="3" stroke-linecap="round" stroke-linejoin="round">
    <path d="M18 3h24l15 15v24L42 57H18L3 42V18z"/>
    <path d="M30 16v20M22 29l8 8 8-8M19 44h22"/>
  </svg>
  <div class="step-num" style="left:514px;top:2776px">01</div>
  <div class="step-num" style="left:614px;top:2776px">03</div>
  <svg class="step-icon" style="left:694px;top:2716px" viewBox="0 0 60 60" aria-hidden="true" fill="none" stroke="#232945" stroke-width="3" stroke-linecap="round" stroke-linejoin="round">
    <path d="M18 3h24l15 15v24L42 57H18L3 42V18z"/>
    <path d="M20 15h20v30H20zM25 24h10M25 31h10M25 38h6"/>
  </svg>
  <div class="step" style="left:770px;top:2724px"><h4>Input scouting data</h4><div class="rule"></div><p>Sed ut perspiciatis unde omnis iste<br>natus error sit voluptatem</p></div>

  <!-- row 2 -->
  <div class="step left" style="left:170px;top:2904px"><h4>Install locally</h4><div class="rule"></div><p>Sed ut perspiciatis unde omnis iste<br>natus error sit voluptatem</p></div>
  <svg class="step-icon" style="left:446px;top:2896px" viewBox="0 0 60 60" aria-hidden="true" fill="none" stroke="#232945" stroke-width="3" stroke-linecap="round" stroke-linejoin="round">
    <path d="M18 3h24l15 15v24L42 57H18L3 42V18z"/>
    <path d="M15 18h30v20H15zM24 45h12M30 38v7"/>
  </svg>
  <div class="step-num" style="left:514px;top:2872px">02</div>
  <div class="step-num" style="left:614px;top:2872px">04</div>
  <svg class="step-icon" style="left:694px;top:2896px" viewBox="0 0 60 60" aria-hidden="true" fill="none" stroke="#232945" stroke-width="3" stroke-linecap="round" stroke-linejoin="round">
    <path d="M18 3h24l15 15v24L42 57H18L3 42V18z"/>
    <path d="M20 14h14l7 7v25H20zM25 30h11M25 37h11"/>
  </svg>
  <div class="step" style="left:770px;top:2904px"><h4>Generate A4 executive PDF</h4><div class="rule"></div><p>Sed ut perspiciatis unde omnis iste<br>natus error sit voluptatem</p></div>

  <span class="abs btn" style="left:488px;top:3096px;width:224px">Get started now</span>
</section>

<!-- DEMO -->
<section class="demo">
  <div class="abs" style="left:480px;top:3300px;width:720px;height:760px;background:var(--lavender);border-radius:380px 0 0 380px"></div>
  <div class="placeholder" role="img" aria-label="Hand holding a tablet with scouting report charts" style="left:-150px;top:3286px;width:690px;height:690px;border-radius:50%;background:radial-gradient(circle at 60% 40%,#dfe3ea,#8d99ad 60%,#3b4560)"></div>
  <div class="placeholder" role="img" aria-label="Football player striking a ball at night" style="left:140px;top:3774px;width:306px;height:306px;border-radius:50%;border:8px solid var(--white);background:radial-gradient(circle at 55% 45%,#8a2430,#2a1a22 55%,#0e0f16)"></div>
  <h2 class="abs display" style="left:552px;top:3348px;font-size:40px"><b style="font-weight:800">Request</b> <span style="font-weight:400">a demo</span></h2>
  <div class="demo-form">
    <div class="field" style="left:560px;top:3524px;width:240px">Enter Name</div>
    <div class="field" style="left:820px;top:3524px;width:244px">Enter Email</div>
    <div class="field" style="left:560px;top:3596px;width:240px">Enter Phone</div>
    <div class="field" style="left:820px;top:3596px;width:244px">Address</div>
    <div class="field area" style="left:560px;top:3668px;width:504px">Message</div>
    <span class="abs btn" style="left:560px;top:3824px;height:34px">Submit message</span>
  </div>
</section>

<!-- FAQ -->
<section class="faq">
  <h2 class="section-title display" style="top:4156px"><b>Our</b> <span>FAQ's</span></h2>
  <div class="faq-item" style="top:4252px">Why Sed ut perspiciatis unde omnis iste natus error sit voluptatdoloremqu?<span class="toggle"></span></div>
  <div class="faq-item" style="top:4324px">Why Sed ut perspiciatis unde omnis iste natus error sit voluptatdoloremqu?<span class="toggle"></span></div>
  <div class="faq-item" style="top:4396px">Why Sed ut perspiciatis unde omnis iste natus error sit voluptatdoloremqu?<span class="toggle"></span></div>
  <div class="faq-item" style="top:4468px">Why Sed ut perspiciatis unde omnis iste natus error sit voluptatdoloremqu?<span class="toggle"></span></div>
  <div class="faq-item open" style="top:4540px">Why Sed ut perspiciatis unde omnis iste natus error sit voluptatdoloremqu?<span class="toggle"></span>
    <p>Nemo enim ipsam voluptatem quia voluptas sit aspernatur aut odit aut fugit, sed quia consequuntur magni dolores eos qui ratione voluptatem sequi nesciunt. Neque porro quisquam est, qui dolorem ipsum quia dolor sit amet, consectetur, adipisci velit, sed quia non.</p>
  </div>
  <span class="abs btn" style="left:500px;top:4704px;width:200px">View more FAQ's</span>
</section>

<!-- FOOTER -->
<footer class="abs site-footer">
  <svg class="abs" style="left:0;top:0" width="1200" height="452" viewBox="0 0 1200 452" aria-hidden="true">
    <path d="M0 40C300 0 800 0 1200 30V452H0Z" fill="#252b45"/>
  </svg>
  <div class="contact-row">
    <div class="contact-item"><span class="ic"><svg width="16" height="20" viewBox="0 0 16 20"><path d="M8 1a6 6 0 016 6c0 5-6 12-6 12S2 12 2 7a6 6 0 016-6z" fill="#252b45"/><circle cx="8" cy="7" r="2" fill="#fff"/></svg></span><span>4210 Harbor Lane, Suite 12<br>Northfield, ON 00000</span></div>
    <div class="contact-item phone"><span class="ic"><svg width="18" height="18" viewBox="0 0 18 18"><path d="M4 1l3 4-2 2c1 2 3 4 5 5l2-2 4 3-2 3C8 16 2 10 1 4z" fill="#252b45"/></svg></span>+1 555 014 2288</div>
    <div class="contact-item"><span class="ic"><svg width="20" height="14" viewBox="0 0 20 14"><rect x="1" y="1" width="18" height="12" fill="none" stroke="#252b45" stroke-width="2"/><path d="M1 1l9 7 9-7" fill="none" stroke="#252b45" stroke-width="2"/></svg></span>info@merivantalo.com</div>
  </div>
  <nav class="footer-nav"><span>Home</span><span>Product</span><span>Packages</span><span>Demo</span><span>How it works</span><span>FAQ's</span><span>Contact</span><span>Purchase</span></nav>
  <div class="footer-rule"></div>
  <p class="copyright">© 2026 Merivantalo All Rights Reserved &nbsp;|&nbsp; Privacy Policy &nbsp;|&nbsp; Terms of use</p>
  <div class="socials"><span></span><span></span><span></span><span></span></div>
</footer>

</body>
</html>
```